National online rug retailer needs a home page design

See the FloorNest logo and create a home page design around that color theme. Details are spelled out in word document uploaded below.

Apparently this website did not take my attachement showing the logo and basic requirements.  If you would send me your email address, I will send you the attachment directly.
Best regards,
Tom Vance
tvance@mrdcorp.example

Target Market(s)

The target market is home owners 25 to 75 years old with combined incomes over $100,000 per year.

Industry/Entity Type

Online

Requirements
Must have
• Lots of white space with black letters and creative use of red and possibly one other color. Would like a compelling call to action button.

```html
<!DOCTYPE html>
<html lang="en">
<head>
<meta charset="utf-8">
<title>FloorNest.com – Home</title>
<link href="https://fonts.googleapis.com/css2?family=Raleway:wght@400;500;600;700&family=Bebas+Neue&display=swap" rel="stylesheet">
<style>
:root{
  --red:#e0141b;
  --ink:#222;
  --text:#444;
  --muted:#777;
  --nav:#3b3b3b;
  --nav-line:#555;
  --side:#5a5a5a;
  --side-line:#6c6c6c;
  --panel:#e9e9e9;
  --footer:#efefef;
  --white:#fff;
}
*{box-sizing:border-box;margin:0;padding:0}
html,body{width:933px;height:1200px;overflow:hidden;background:var(--white)}
body{font-family:'Raleway',Arial,sans-serif;color:var(--text);position:relative}
a{color:inherit;text-decoration:none}
.abs{position:absolute}

/* header */
.brand{left:93px;top:14px;display:flex;align-items:center;gap:8px}
.brand-mark{width:26px;height:26px;background:var(--red)}
.brand-name{font-size:31px;font-weight:600;color:var(--ink);letter-spacing:-.5px}
.tagline{left:173px;top:66px;font-size:10px;color:var(--muted)}
.utility{right:93px;top:12px;display:flex;gap:12px;font-size:10px;color:#555;align-items:center}
.utility b{font-weight:600;color:#333}
.cart{right:93px;top:36px;display:flex;align-items:center;gap:6px;font-size:11px;color:#555}
.phone{right:93px;top:59px;font-size:15px;font-weight:600;color:#555}
.phone span{color:var(--red)}

/* nav */
.nav{left:93px;top:92px;width:747px;height:41px;background:var(--nav);border-bottom:4px solid var(--red);display:flex}
.nav a{flex:none;color:#fff;font-size:12.5px;font-weight:500;line-height:37px;text-align:center;white-space:nowrap;border-right:1px solid var(--nav-line)}
.nav a.active{background:var(--red);font-weight:700}
.nav .more{display:flex;align-items:center;justify-content:center;border-right:0}

/* sidebar */
.search{left:93px;top:137px;width:186px;height:34px;background:var(--panel);display:flex;align-items:center;justify-content:space-between;padding:0 9px;font-size:11px;color:#333}
.cats{left:93px;top:171px;width:186px;background:var(--side)}
.cats h2{background:#333;color:#fff;font-family:'Bebas Neue',sans-serif;font-weight:400;font-size:22px;letter-spacing:.5px;height:38px;line-height:41px;padding-left:9px}
.cats li{list-style:none;height:28.7px;border-bottom:1px solid var(--side-line);color:#fff;font-size:10.5px;display:flex;align-items:center;padding:0 10px}
.cats li::before{content:"";width:5px;height:5px;border-radius:50%;background:#fff;margin-right:12px}
.cats li i{margin-left:auto;width:8px;height:8px;background:#111;color:#fff;font-style:normal;font-size:8px;line-height:8px;text-align:center}

/* hero */
.hero{left:279px;top:137px;width:561px;height:329px;background:linear-gradient(160deg,#6b625a 0%,#c9bcab 35%,#e4ddd2 60%,#8a7a6a 100%)}
.caption{left:279px;top:364px;width:397px;height:78px;background:rgba(238,238,238,.92);padding:9px 10px}
.caption h1{font-family:'Bebas Neue',sans-serif;font-weight:400;font-size:30px;line-height:28px;color:#555}
.caption h1 span{color:var(--red)}
.caption p{font-size:8.6px;line-height:13px;color:#333;margin-top:4px;width:360px}
.arrows{left:676px;top:364px;width:27px;height:78px;background:var(--red);display:flex;flex-direction:column;justify-content:space-around;align-items:center}

.section-title{font-size:17px;font-weight:500;color:var(--red)}

/* side list */
.mini{left:93px;width:160px;height:78px;display:flex;gap:9px}
.mini .thumb{width:78px;height:77px;flex:none}
.mini h3{font-size:10.5px;font-weight:500;color:#555;line-height:13px;margin-top:1px}
.mini .now{color:var(--red);font-size:11px;margin-top:7px}
.mini .was{color:#444;font-size:10px;text-decoration:line-through}
.rule{left:93px;width:160px;height:1px;background:#ccc}

/* cards */
.card{width:177px;height:184px;border:1px solid #ddd}
.card .img{height:117px}
.card .desc{background:var(--red);color:#fff;font-size:10px;line-height:13.5px;padding:4px 6px;height:37px}
.card .buy{display:flex;height:29px;align-items:center;background:var(--panel)}
.card .price{flex:1;font-size:11px;padding-left:6px;color:#444}
.card .details{width:67px;height:100%;background:#000;color:#fff;font-size:11px;font-weight:700;display:flex;align-items:center;justify-content:center}

/* footer */
.footer{left:0;top:935px;width:933px;height:265px;background:var(--footer)}
.col{top:950px}
.col h4{font-size:12px;font-weight:500;color:#444;margin-bottom:8px}
.col li{list-style:none;font-size:9px;color:#333;line-height:18px}
.badges{left:593px;top:975px;display:flex;gap:5px}
.badges span{width:23px;height:15px;border-radius:2px}
.seals{left:590px;top:1015px;display:flex;gap:6px;align-items:center}
.bottom-rule{left:93px;top:1162px;width:747px;height:1px;background:#d6d6d6}
.copy{left:105px;top:1174px;font-size:9px;color:#555}
.legal{right:105px;top:1174px;font-size:9px;color:#555}
</style>
</head>
<body>

<header>
  <a class="abs brand" href="#"><span class="brand-mark"></span><span class="brand-name">FloorNest.com</span></a>
  <div class="abs tagline">rugs made for every room you love</div>
  <nav class="abs utility">
    <a href="#">My Account</a><a href="#">My Wishlist</a><a href="#">My Cart</a><a href="#">Chech Out</a><a href="#">Login</a>
    <b>En ▾</b><b>$ ▾</b>
    <svg width="10" height="12" viewBox="0 0 10 12"><rect x="0" y="5" width="10" height="7" fill="#555"/><path d="M2 5V3.5a3 3 0 0 1 6 0V5" fill="none" stroke="#555" stroke-width="1.6"/></svg>
  </nav>
  <div class="abs cart">
    <svg width="22" height="18" viewBox="0 0 22 18"><path d="M0 1h4l3 10h11l3-8H6" fill="none" stroke="#555" stroke-width="2"/><circle cx="8" cy="15" r="2" fill="#555"/><circle cx="17" cy="15" r="2" fill="#555"/></svg>
    <span>Cart &nbsp; ( empty ) &nbsp; ▾</span>
  </div>
  <div class="abs phone">Order Toll-Free : <span>1-888-555-0142</span></div>
</header>

<nav class="abs nav">
  <a class="active" href="#" style="width:55px">Home</a>
  <a href="#" style="width:114px">Selection Guide</a>
  <a href="#" style="width:80px">Rug Care</a>
  <a href="#" style="width:49px">FAQ</a>
  <a href="#" style="width:98px">Return Policy</a>
  <a href="#" style="width:101px">Free Shipping</a>
  <a href="#" style="width:106px">Clearance Rug</a>
  <a href="#" style="width:88px">Contact Us</a>
  <a class="more" href="#" style="width:56px"><svg width="16" height="16" viewBox="0 0 16 16"><path d="M8 1v14M1 8h14" stroke="#fff" stroke-width="3.5"/></svg></a>
</nav>

<aside>
  <div class="abs search"><span>Enter keyword or items...</span>
    <svg width="14" height="14" viewBox="0 0 14 14"><circle cx="5.5" cy="5.5" r="4.3" fill="none" stroke="#222" stroke-width="1.8"/><path d="M8.7 8.7L13 13" stroke="#222" stroke-width="2"/></svg>
  </div>
  <div class="abs cats">
    <h2>Categories</h2>
    <ul>
      <li>RUG THEME<i>+</i></li><li>COLOR WAY<i>+</i></li><li>SIZE<i>+</i></li><li>SHAPE<i>+</i></li><li>FIBER CONTENT<i>+</i></li><li>MFGR. BRAND<i>+</i></li><li>MFGR.COLLECTION<i>+</i></li><li>PRICE<i>+</i></li><li>RUG PATTERN<i>+</i></li>
    </ul>
  </div>
</aside>

<section>
  <div class="abs hero" role="img" aria-label="Living room with a cream sectional sofa on a light carved rug"></div>
  <div class="abs caption">
    <h1>Lorem ipsum <span>dolor sit amet</span></h1>
    <p>Lorem ipsum dolor sit amet, consectetur adipisicing elit, sed do eiusmod tempor incididunt ut labore et dolore magna aliqua. Ut enim ad minim veniam,</p>
  </div>
  <div class="abs arrows">
    <svg width="7" height="8" viewBox="0 0 7 8"><path d="M0 0l7 4-7 4z" fill="#fff"/></svg>
    <svg width="7" height="8" viewBox="0 0 7 8"><path d="M7 0L0 4l7 4z" fill="#fff"/></svg>
  </div>
</section>

<h2 class="abs section-title" style="left:93px;top:482px">You Make Also Like</h2>
<h2 class="abs section-title" style="left:283px;top:482px">Featured Products</h2>

<div class="abs mini" style="top:518px"><div class="thumb" role="img" aria-label="Blue shag rug underfoot" style="background:linear-gradient(135deg,#c9c2bb,#6f87a8)"></div><div><h3>LOREM IPSUM DOLOR</h3><div class="now">$90.00</div><div class="was">$100.00</div></div></div>
<div class="abs rule" style="top:609px"></div>
<div class="abs mini" style="top:624px"><div class="thumb" role="img" aria-label="Sofa on a light patterned rug" style="background:linear-gradient(160deg,#5d554d,#d9cfc2)"></div><div><h3>LOREM IPSUM DOLOR</h3><div class="now">$90.00</div><div class="was">$100.00</div></div></div>
<div class="abs rule" style="top:715px"></div>
<div class="abs mini" style="top:729px"><div class="thumb" role="img" aria-label="Rolled red and green patterned rugs" style="background:linear-gradient(150deg,#b23a2a,#8c8a3a)"></div><div><h3>LOREM IPSUM DOLOR</h3><div class="now">$90.00</div><div class="was">$100.00</div></div></div>
<div class="abs rule" style="top:820px"></div>
<div class="abs mini" style="top:834px"><div class="thumb" role="img" aria-label="Red and yellow checked shag rug" style="background:linear-gradient(135deg,#e0a020,#c4321c)"></div><div><h3>LOREM IPSUM DOLOR</h3><div class="now">$90.00</div><div class="was">$100.00</div></div></div>

<div class="abs card" style="left:283px;top:517px"><div class="img" role="img" aria-label="Cream sheepskin rug on wood floor" style="background:linear-gradient(170deg,#f4efe6 65%,#a5633a)"></div><div class="desc">Lorem ipsum dolor sit amet conse cteture adipisicing.</div><div class="buy"><span class="price">$90.00</span><a class="details" href="#">DETAILS</a></div></div>
<div class="abs card" style="left:474px;top:517px"><div class="img" role="img" aria-label="White flokati rug beside a chair" style="background:linear-gradient(180deg,#6b5a48,#efebe3 40%)"></div><div class="desc">Lorem ipsum dolor sit amet conse cteture adipisicing.</div><div class="buy"><span class="price">$90.00</span><a class="details" href="#">DETAILS</a></div></div>
<div class="abs card" style="left:663px;top:517px"><div class="img" role="img" aria-label="Red Persian style rug" style="background:linear-gradient(135deg,#7a2320,#3b3040 50%,#8e2a24)"></div><div class="desc">Lorem ipsum dolor sit amet conse cteture adipisicing.</div><div class="buy"><span class="price">$90.00</span><a class="details" href="#">DETAILS</a></div></div>
<div class="abs card" style="left:283px;top:728px"><div class="img" role="img" aria-label="Lavender trellis pattern rug" style="background:linear-gradient(135deg,#b9b4d6,#e6e2ee)"></div><div class="desc">Lorem ipsum dolor sit amet conse cteture adipisicing.</div><div class="buy"><span class="price">$90.00</span><a class="details" href="#">DETAILS</a></div></div>
<div class="abs card" style="left:474px;top:728px"><div class="img" role="img" aria-label="Dark brown rug with colored circles" style="background:linear-gradient(135deg,#a8602e,#2b1d17 40%,#3a2a20)"></div><div class="desc">Lorem ipsum dolor sit amet conse cteture adipisicing.</div><div class="buy"><span class="price">$90.00</span><a class="details" href="#">DETAILS</a></div></div>
<div class="abs card" style="left:663px;top:728px"><div class="img" role="img" aria-label="Red and yellow checked shag rug" style="background:linear-gradient(135deg,#e8a820,#cc3a1c)"></div><div class="desc">Lorem ipsum dolor sit amet conse cteture adipisicing.</div><div class="buy"><span class="price">$90.00</span><a class="details" href="#">DETAILS</a></div></div>

<footer>
  <div class="abs footer"></div>
  <div class="abs col" style="left:107px"><h4>Customer Services</h4><ul><li>Shipping</li><li>Return Policy</li><li>Privacy Policy</li><li>Ordering &amp; Delivery Checklist</li><li>Terms of Use</li><li>Terms of Sale</li><li>Contact Us</li><li>Environmental Policy</li></ul></div>
  <div class="abs col" style="left:280px"><h4>Resources</h4><ul><li>Product Articles</li><li>Learning Center</li><li>Help</li><li>Refer A Friend</li><li>FloorNest Blog</li><li>Room Scene Viewer</li><li>Site Map</li><li>FAQ</li><li>Customer Testimonials</li><li>Photo Gallery</li></ul></div>
  <div class="abs col" style="left:442px"><h4>Corporate Info</h4><ul><li>About FloorNest.com</li><li>Careers</li><li>Affiliates</li></ul></div>
  <div class="abs col" style="left:593px"><h4>Payment &amp; Shipping</h4></div>
  <div class="abs badges">
    <span style="background:#2a3a8a"></span><span style="background:#d8d8d8"></span><span style="background:#1a3d9a"></span><span style="background:#3a88c8"></span><span style="background:#e8c23a"></span>
    <span style="width:90px;height:22px;margin-top:-4px;background:#d0d8e6"></span>
  </div>
  <div class="abs seals">
    <span style="width:34px;height:34px;border-radius:50%;background:#c9b34a;display:block"></span>
    <span style="width:32px;height:32px;border-radius:50%;background:#e0c33c;display:block"></span>
    <span style="width:48px;height:20px;background:#bbb;display:block"></span>
    <span style="width:48px;height:22px;background:#2a5c9c;display:block"></span>
    <span style="width:56px;height:24px;background:#9aa;display:block"></span>
  </div>
  <div class="abs bottom-rule"></div>
  <div class="abs copy">© 2013 FloorNest All Rights Reserved.</div>
  <div class="abs legal">Terms &amp; Condition &nbsp; | &nbsp; Privacy Policy</div>
</footer>

</body>
</html>
```